Direct Cremation Campaign

I need a post card design that can be used for flyers, newspapers, and magazines. I have enclosed an example

Target Market(s)

Funeral- direct cremation

Industry/Entity Type

Funeral Home

Font styles to use
Serif

Colors

Designer to choose colors to be used in the design.

Requirements
Must have
• See uploaded picture as example
Nice to have
Should not have

```html
<!DOCTYPE html>
<html lang="en">
<head>
<meta charset="utf-8">
<title>Direct Cremation Campaign – Flyer and Postcard</title>
<link href="https://fonts.googleapis.com/css2?family=Tinos:wght@400;700&family=Cinzel:wght@400;600&display=swap" rel="stylesheet">
<style>
  :root{
    --red:#d6302f;
    --red-dark:#b8201f;
    --blue:#23388c;
    --blue-dark:#1a2a6e;
    --white:#ffffff;
    --grey:#e4e4e4;
    --ink:#2b2b2b;
    --cream:#fbeede;
    --stage:#ece7df;
  }
  *{box-sizing:border-box;margin:0;padding:0}
  html,body{width:1200px;height:730px;overflow:hidden}
  body{background:var(--stage);position:relative;font-family:"Tinos",serif;color:var(--ink)}

  /* ---------- Flyer ---------- */
  .flyer{position:absolute;left:51px;top:66px;width:461px;height:600px;background:var(--red);overflow:hidden;box-shadow:0 6px 14px rgba(0,0,0,.25)}
  .flyer-header{position:absolute;left:0;top:0;width:461px;height:160px}
  .brand{position:absolute;display:flex;align-items:center;gap:8px;font-family:"Tinos",serif;font-weight:400;color:var(--ink)}
  .brand-mark{flex:none;border:2px solid var(--ink);border-radius:50%}
  .flyer .brand{left:88px;top:44px;font-size:22px;white-space:nowrap}
  .flyer .brand-mark{width:30px;height:30px}

  .urn-photo{position:absolute;border-radius:40% 40% 22% 22% / 30% 30% 14% 14%}
  .urn-left{left:41px;top:153px;width:100px;height:204px;background:linear-gradient(160deg,#6b2a2e,#2a1214)}
  .urn-right{left:322px;top:153px;width:100px;height:204px;background:linear-gradient(160deg,#5d86b8,#1f3558)}

  .price-tag{position:absolute;width:72px;height:28px;background:var(--blue);border:1.5px solid var(--white);border-radius:4px;color:var(--white);font-weight:700;font-size:15px;display:flex;align-items:center;justify-content:center;white-space:nowrap}
  .tag-low{left:-6px;top:206px;transform:rotate(-65deg)}
  .tag-high{left:396px;top:206px;width:84px;transform:rotate(65deg);font-size:13px}

  .headline{position:absolute;color:var(--white);font-family:"Tinos",serif;line-height:1;white-space:nowrap}
  .flyer .hl-see{left:148px;top:161px;font-size:115px;letter-spacing:-3px}
  .flyer .hl-can{left:201px;top:176px;font-size:30px}
  .flyer .hl-diff{left:151px;top:266px;font-size:28px}

  .guarantee-badge{position:absolute;left:189px;top:291px;width:72px;height:72px;border-radius:50%;background:radial-gradient(circle,#f7c531 0 55%,#e0202a 56% 100%);border:3px solid #f3d36b}

  .caption{position:absolute;top:335px;font-family:"Cinzel",serif;font-size:10.5px;color:var(--cream);text-align:center;line-height:1.3}
  .caption-left{left:26px;width:130px}
  .caption-right{left:274px;width:182px}

  .savings-band{position:absolute;left:0;top:367px;width:461px;height:43px;background:var(--grey);font-weight:700;font-size:13px;text-align:center;line-height:1.3;padding-top:5px;color:#333}

  .services{position:absolute;left:0;top:410px;width:461px;height:157px;background:var(--blue)}
  .services-title{position:absolute;left:0;width:100%;top:7px;text-align:center;color:var(--white);font-weight:700;font-size:17px}
  .services-title span{border-bottom:1.5px solid var(--white);padding:0 2px 2px}
  .service{position:absolute;top:41px;width:120px;text-align:center;color:var(--white);font-size:11.5px;white-space:nowrap}
  .service-photo{display:block;margin:0 auto 14px;width:67px;height:67px;border-radius:50%;border:3px solid var(--white)}
  .service-divider{position:absolute;top:42px;width:1px;height:104px;background:rgba(255,255,255,.6)}
  .sv1{left:8px}.sv2{left:132px}.sv3{left:245px}.sv4{left:346px}
  .sv1 .service-photo{background:linear-gradient(135deg,#2d2d33,#8b7868)}
  .sv2 .service-photo{background:linear-gradient(135deg,#7c7266,#b9b0a2)}
  .sv3 .service-photo{background:linear-gradient(135deg,#c98fbf,#5d8a4a)}
  .sv4 .service-photo{background:linear-gradient(135deg,#f0c9d4,#8d8f92)}

  .contact-bar{position:absolute;left:0;bottom:0;width:461px;height:33px;background:var(--red-dark);display:flex;align-items:center;justify-content:center;gap:8px;color:var(--white)}
  .contact-bar .phone{font-weight:700;font-size:22px}
  .contact-bar .web{font-size:15px}
  .contact-bar .sep{font-size:18px}
  .icon{width:17px;height:17px;flex:none}

  /* ---------- Postcard ---------- */
  .postcard{position:absolute;left:546px;top:133px;width:604px;height:465px;background:var(--white);overflow:hidden;box-shadow:0 6px 14px rgba(0,0,0,.25)}
  .postcard-shapes{position:absolute;left:0;top:0}
  .pc-title{position:absolute;left:16px;top:25px;color:var(--white);font-weight:700;font-size:24px;white-space:nowrap}
  .pc-sub{position:absolute;left:14px;top:52px;width:236px;color:var(--white);font-size:12px;text-align:center;line-height:1.3}
  .pc-sub b{font-weight:700}
  .postcard .hl-see{left:14px;top:76px;font-size:80px;letter-spacing:-2px}
  .postcard .hl-can{left:53px;top:85px;font-size:20px}
  .postcard .hl-diff{left:124px;top:117px;font-size:28px}
  .pc-offer{position:absolute;left:15px;top:150px;font-family:"Cinzel",serif;font-weight:600;font-size:10px;color:var(--white);white-space:nowrap}
  .pc-urns{position:absolute;left:15px;top:181px;width:250px;height:206px;border-radius:14px;background:linear-gradient(100deg,#f2f0ea 0 30%,#a98aa8 45% 65%,#3b5f8f 80%)}
  .pc-phone{position:absolute;left:20px;top:409px;display:flex;align-items:center;gap:12px;color:var(--white);font-weight:700;font-size:28px;white-space:nowrap}
  .pc-web{position:absolute;left:24px;top:440px;display:flex;align-items:center;gap:10px;color:var(--white);font-size:14px;white-space:nowrap}
  .pc-web .icon{width:15px;height:15px}
  .pc-phone .icon{width:22px;height:22px}
  .postcard .brand{left:336px;top:38px;width:150px;font-size:15px;line-height:1.2}
  .postcard .brand-mark{width:24px;height:24px}
  .stamp-box{position:absolute;left:500px;top:24px;width:87px;height:81px;border:1px solid #333}
  .address-line{position:absolute;left:369px;width:210px;height:1px;background:#555}
</style>
</head>
<body>

<section class="flyer">
  <svg class="flyer-header" viewBox="0 0 461 160" aria-hidden="true">
    <path d="M0 0H461V70C380 110 260 140 150 128C90 122 40 105 0 85Z" fill="#f4f4f4"/>
    <path d="M0 85C40 105 90 122 150 128C260 140 380 110 461 70V98C380 140 260 158 150 150C90 144 40 120 0 96Z" fill="#23388c"/>
  </svg>
  <div class="brand"><span class="brand-mark"></span>Harlow Funeral &amp; Cremation</div>

  <div class="urn-photo urn-left" role="img" aria-label="Dark red speckled cremation urn"></div>
  <div class="urn-photo urn-right" role="img" aria-label="Blue speckled cremation urn"></div>
  <div class="price-tag tag-low">$795</div>
  <div class="price-tag tag-high">Up to $2,500</div>

  <div class="headline hl-see">See</div>
  <div class="headline hl-can">Can You</div>
  <div class="headline hl-diff">the Difference</div>
  <div class="guarantee-badge" role="img" aria-label="Guarantee seal"></div>

  <p class="caption caption-left">Harlow Funeral and<br>Cremation Price - $795</p>
  <p class="caption caption-right">Average cost of a cremation in<br>the Capital Region - $2,500</p>

  <p class="savings-band">The Only Difference You’ll See In Harlow Funeral and Cremation Service is<br>The Amount Of Money You Will Save</p>

  <div class="services">
    <h2 class="services-title"><span>OUR SERVICES</span></h2>
    <div class="service sv1"><span class="service-photo" role="img" aria-label="Funeral service photo"></span>FUNERAL SERVICE</div>
    <div class="service-divider" style="left:129px"></div>
    <div class="service sv2"><span class="service-photo" role="img" aria-label="Memorial plaque photo"></span>MEMORIAL SERVICE</div>
    <div class="service-divider" style="left:255px"></div>
    <div class="service sv3"><span class="service-photo" role="img" aria-label="Burial flowers photo"></span>BURIAL</div>
    <div class="service-divider" style="left:355px"></div>
    <div class="service sv4"><span class="service-photo" role="img" aria-label="Urn with flowers photo"></span>CREMATION</div>
  </div>

  <div class="contact-bar">
    <svg class="icon" viewBox="0 0 24 24" aria-hidden="true"><path d="M6.6 10.8a15 15 0 0 0 6.6 6.6l2.2-2.2a1 1 0 0 1 1-.25 11.4 11.4 0 0 0 3.6.57 1 1 0 0 1 1 1V20a1 1 0 0 1-1 1A17 17 0 0 1 3 4a1 1 0 0 1 1-1h3.5a1 1 0 0 1 1 1c0 1.25.2 2.45.57 3.57a1 1 0 0 1-.25 1Z" fill="#fff"/></svg>
    <span class="phone">(555) 014-2270</span>
    <span class="sep">|</span>
    <svg class="icon" viewBox="0 0 24 24" aria-hidden="true"><g fill="none" stroke="#fff" stroke-width="1.6"><circle cx="12" cy="12" r="9"/><ellipse cx="12" cy="12" rx="4" ry="9"/><path d="M3 12h18M5 7h14M5 17h14"/></g></svg>
    <span class="web">www.harlowcremations.com</span>
  </div>
</section>

<section class="postcard">
  <svg class="postcard-shapes" width="604" height="465" viewBox="0 0 604 465" aria-hidden="true">
    <path d="M0 0H318C392 110 392 330 246 465H0Z" fill="#d6302f"/>
    <path d="M0 0H284C346 110 346 300 262 399H0Z" fill="#23388c"/>
  </svg>
  <h1 class="pc-title">Live Well, Plan Ahead</h1>
  <p class="pc-sub">Planning Ahead Can Make All the Difference to<br><b>Your Family</b></p>
  <div class="headline hl-see">See</div>
  <div class="headline hl-can">Can You</div>
  <div class="headline hl-diff">The Difference</div>
  <p class="pc-offer">Cremation for $795 all fees(crematory) included!</p>
  <div class="pc-urns" role="img" aria-label="White, lilac and blue cremation urns"></div>

  <div class="pc-phone">
    <svg class="icon" viewBox="0 0 24 24" aria-hidden="true"><path d="M6.6 10.8a15 15 0 0 0 6.6 6.6l2.2-2.2a1 1 0 0 1 1-.25 11.4 11.4 0 0 0 3.6.57 1 1 0 0 1 1 1V20a1 1 0 0 1-1 1A17 17 0 0 1 3 4a1 1 0 0 1 1-1h3.5a1 1 0 0 1 1 1c0 1.25.2 2.45.57 3.57a1 1 0 0 1-.25 1Z" fill="#fff"/></svg>
    (555) 014-2270
  </div>
  <div class="pc-web">
    <svg class="icon" viewBox="0 0 24 24" aria-hidden="true"><g fill="none" stroke="#fff" stroke-width="1.6"><circle cx="12" cy="12" r="9"/><ellipse cx="12" cy="12" rx="4" ry="9"/><path d="M3 12h18M5 7h14M5 17h14"/></g></svg>
    www.harlowcremations.com
  </div>

  <div class="brand"><span class="brand-mark"></span><span>Harlow Funeral &amp;<br>Cremation</span></div>
  <div class="stamp-box"></div>
  <div class="address-line" style="top:269px"></div>
  <div class="address-line" style="top:308px"></div>
  <div class="address-line" style="top:345px"></div>
</section>

</body>
</html>
```